Fun Employee News and Engagement Portal - Tidy Hearth Company

We are looking for a clean, but fun WordPress template for an internal employee engagement website. The site will be a place we share news, fun stories and pictures. We'll provide space for our employees to post comments, etc.
We are a deep dish pizza restaurant with a rich history. I'd love to see your take on a look and feel for us! The site will be called Bim-Zee. I've posted some images and colors along with this brief description.
Focus on making the template whimsical and fun! (Extra point for focusing on the "Lettering in lights" ).
I will continue to post additional pieces of art and content examples.
Reason: Our team is continuing to review designs. We've decided to extend the timing a few more days. Good luck! Make it playful!
Reason: We need more time with our team to review these designs. We are going to extend one more time!
Reason: Still trying to get enough time to review with the Bim-Zee team!
Reason: We are continuing to evaluate designs. Thank you!
Industry/Entity Type
American Restaurant
Number of Pages Required
1 page
Look and feel
Each slider illustrates characteristics of the customer's brand and the style your logo design should communicate.

```html
<!DOCTYPE html>
<html lang="en">
<head>
<meta charset="utf-8">
<title>Bim-Zee — Tidy Hearth Company</title>
<link href="https://fonts.googleapis.com/css2?family=Roboto+Slab:wght@400;700&family=Roboto:wght@400;500;700&display=swap" rel="stylesheet">
<style>
:root{
  --red:#e3202a;
  --ink:#222;
  --text:#333;
  --light:#999;
  --rule:#e6e6e6;
  --footer:#f1f1f1;
  --pagebook:#3b5998;
  --chirper:#2ebbed;
  --viewtube:#6d6d6d;
  --snapgram:#9d8a6c;
}
*{box-sizing:border-box;margin:0;padding:0}
html,body{width:1200px;height:3333px;overflow:hidden}
body{position:relative;background:#fff;font-family:"Roboto",Arial,sans-serif;color:var(--text)}
.abs{position:absolute}
.photo{display:block}
svg.ico{width:12px;height:12px;fill:var(--red);vertical-align:-1px;margin-right:4px}

/* header */
.topline{left:0;top:0;width:1200px;height:4px;background:var(--red)}
.logo{font-family:"Roboto Slab",Georgia,serif;font-weight:700;color:var(--red)}
.site-header .logo{left:98px;top:16px;font-size:38px;line-height:50px}
.main-nav{right:98px;top:30px;display:flex;gap:30px;font-size:13px;color:#444;text-transform:uppercase;align-items:center}
.main-nav .sep{width:1px;height:14px;background:var(--red);margin:0 -18px}
.main-nav svg{width:13px;height:13px;fill:none;stroke:var(--red);stroke-width:2.4}

/* hero */
.hero{left:0;top:80px;width:1200px;height:444px;background:radial-gradient(ellipse at 50% 55%,#8a3a22 0%,#5a2a18 45%,#2e1a12 100%)}
.hero-photo{position:absolute;inset:0;background:linear-gradient(110deg,rgba(60,30,18,.2),rgba(140,50,30,.25) 40%,rgba(40,25,18,.2) 70%,rgba(220,210,190,.35) 95%)}
.hero h1{position:absolute;left:0;right:0;top:100px;text-align:center;font-family:"Roboto Slab",Georgia,serif;font-weight:700;font-size:90px;color:#fff;letter-spacing:2px}
.hero .tagline{position:absolute;left:0;right:0;top:200px;text-align:center;font-family:"Roboto Slab",Georgia,serif;font-size:30px;color:#fff;letter-spacing:7px;font-weight:700}
.hero .btn{position:absolute;left:508px;top:288px;width:184px;height:40px;border:2px solid #fff;color:#fff;font-family:"Roboto Slab",Georgia,serif;font-size:15px;font-weight:700;text-align:center;line-height:36px}
.hero .arrow{position:absolute;top:200px;width:30px;height:70px;fill:none;stroke:#fff;stroke-width:2;opacity:.8}

/* section titles */
.sec-title{height:36px;border-bottom:3px solid var(--red)}
.sec-title span{display:inline-block;height:33px;line-height:34px;background:var(--red);color:#fff;font-family:"Roboto Slab",Georgia,serif;font-weight:700;font-size:15px;text-transform:uppercase;padding:0 44px 0 12px;clip-path:polygon(0 0,calc(100% - 26px) 0,100% 100%,0 100%)}

.meta{font-size:12px;color:var(--light);display:flex;gap:16px}
.title{font-weight:700;color:var(--ink);line-height:1.5}
.excerpt{font-size:11.5px;color:#666;line-height:1.75}

/* reviews */
.review{left:98px;width:637px;height:162px;display:flex;gap:26px}
.review .photo{width:245px;height:162px;flex:none}
.review .title{font-size:17px;margin:12px 0 12px}

/* stories grid */
.story{width:306px}
.story .photo{width:306px;height:168px}
.story .meta{margin-top:16px}
.story .title{font-size:16.5px;margin-top:12px}

/* video */
.video{left:98px;top:1858px;width:637px;height:264px;background:linear-gradient(180deg,#2a1c14,#6b3a20 55%,#3b2416)}
.play{position:absolute;left:298px;top:112px;width:42px;height:42px;fill:none;stroke:#fff;stroke-width:2}
.video-text{left:98px;top:2152px;width:637px;font-size:11.5px;color:#666;line-height:1.75}

/* employees */
.emp{width:195px}
.emp .photo{width:195px;height:120px}
.emp .title{font-size:14px;margin-top:12px;line-height:1.45}
.emp .meta{margin-top:6px;gap:12px;font-size:11.5px}

/* sidebar */
.side{left:800px;width:300px}
.follow a{display:flex;align-items:center;height:36px;margin-bottom:2px;color:#fff;font-size:13px;text-decoration:none}
.follow .sq{width:34px;height:36px;display:flex;align-items:center;justify-content:center;background:rgba(0,0,0,.12)}
.follow .sq i{width:10px;height:10px;border:2px solid #fff;border-radius:2px;display:block}
.follow .count{width:98px;padding-left:14px;font-weight:700}
.popular .photo{width:300px;height:127px}
.popular p{font-size:14px;color:#444;line-height:1.7;margin-top:18px}
.popular .row{display:flex;justify-content:space-between;font-size:10px;color:var(--light);margin-top:10px;text-transform:uppercase}
.comments{left:800px;top:1769px;width:300px;height:289px;background:linear-gradient(160deg,#e8262f,#d51a22);color:#fff;text-align:center;padding:26px 26px 0}
.comments h3{font-family:"Roboto Slab",Georgia,serif;font-size:16px;font-weight:700}
.comments p{font-size:11px;line-height:1.7;margin-top:6px;opacity:.85}
.comments .field{background:#fff;color:var(--light);font-size:11px;text-align:left;padding:8px;height:32px;margin-top:14px}
.comments .field.area{height:76px;margin-top:8px}
.comments .submit{border:2px solid #fff;height:36px;line-height:32px;font-size:13px;font-weight:700;margin-top:12px}
.recent{display:flex;gap:24px;height:92px}
.recent .photo{width:103px;height:92px;flex:none}
.recent .title{font-size:14px;font-weight:400;color:#333;line-height:1.6}
.recent .excerpt{font-size:11px;margin-top:6px;line-height:1.7}

/* gallery */
.divider{left:98px;top:2638px;width:1002px;height:1px;background:var(--rule)}
.gallery-title{left:98px;top:2684px;font-family:"Roboto Slab",Georgia,serif;font-weight:700;font-size:22px;color:var(--ink)}
.gal-nav{left:1050px;top:2686px;display:flex;gap:4px}
.gal-nav svg{width:24px;height:24px;fill:none;stroke:#555;stroke-width:1.5}
.gallery{left:98px;top:2744px;display:flex;gap:17px}
.gallery .photo{width:187px;height:123px}
.partners{left:98px;top:2920px;width:1002px;height:80px;display:flex;align-items:center;justify-content:space-between}
.partner{font-family:"Roboto",Arial,sans-serif;font-weight:700;font-size:24px;color:var(--ink);width:230px;text-align:center}

/* footer */
.site-footer{left:0;top:3051px;width:1200px;height:282px;background:var(--footer);text-align:center}
.site-footer .logo{position:absolute;left:0;right:0;top:58px;font-size:50px;line-height:60px}
.foot-nav{position:absolute;left:0;right:0;top:133px;font-size:13px;color:#333}
.foot-nav b{font-weight:400;color:#888;margin:0 12px}
.socials{position:absolute;left:486px;top:178px;display:flex;gap:12px}
.socials i{width:30px;height:30px;border:2px solid #aaa;border-radius:50%;display:block}
.copy{position:absolute;left:0;right:0;top:226px;font-size:11px;color:#aaa}
</style>
</head>
<body>
<svg width="0" height="0" style="position:absolute" aria-hidden="true">
  <symbol id="i-comment" viewBox="0 0 12 12"><path d="M1 1h10v7H5l-3 3V8H1z"/></symbol>
  <symbol id="i-eye" viewBox="0 0 12 12"><path d="M0 6c2-4 10-4 12 0-2 4-10 4-12 0zm6 2.3a2.3 2.3 0 1 0 0-4.6 2.3 2.3 0 0 0 0 4.6z"/></symbol>
  <symbol id="i-share" viewBox="0 0 12 12"><circle cx="9.5" cy="2.5" r="2.2"/><circle cx="2.5" cy="6" r="2.2"/><circle cx="9.5" cy="9.5" r="2.2"/><path d="M2.5 6 9.5 2.5M2.5 6l7 3.5" stroke="#e3202a" stroke-width="1.2"/></symbol>
</svg>

<div class="abs topline"></div>
<header class="site-header">
  <div class="abs logo">Bim-Zee</div>
  <nav class="abs main-nav">
    <span>Home</span><span>About us</span><span>News</span><span>Funs</span><span>Stories</span><span>Pictures</span><span>Contact us</span><span class="sep"></span>
    <svg viewBox="0 0 14 14"><circle cx="6" cy="6" r="4.5"/><path d="M9.5 9.5 13 13"/></svg>
  </nav>
</header>

<section class="abs hero">
  <div class="hero-photo" role="img" aria-label="Overhead photo of pizzas, tomatoes and mozzarella on a wooden table"></div>
  <svg class="arrow" style="left:40px" viewBox="0 0 30 70"><path d="M26 4 4 35l22 31"/></svg>
  <svg class="arrow" style="right:40px" viewBox="0 0 30 70"><path d="M4 4l22 31L4 66"/></svg>
  <h1>BIM - ZEE</h1>
  <div class="tagline">WE ARE A TIDY HEARTH COMPANY</div>
  <div class="btn">GET MORE INFO</div>
</section>

<div class="abs sec-title" style="left:98px;top:580px;width:637px"><span>Updated Recent Reviews</span></div>

<article class="abs review" style="top:656px">
  <div class="photo" role="img" aria-label="Friends sharing pizza at a table" style="background:linear-gradient(135deg,#c9b9a4,#7a5a44)"></div>
  <div>
    <div class="meta"><span><svg class="ico"><use href="#i-comment"/></svg>562</span><span><svg class="ico"><use href="#i-eye"/></svg>89</span><span><svg class="ico"><use href="#i-share"/></svg>8520</span></div>
    <h3 class="title">It is a long established fact that a reader will be distracted by the readable</h3>
    <p class="excerpt">There are many variations of passages of Lorem Ipsum available, but the majority have suffered alteration in some form, by injected umour, or randomised words which don't look even slightly believable.</p>
  </div>
</article>
<div class="abs" style="left:98px;top:850px;width:637px;height:1px;background:var(--rule)"></div>

<article class="abs review" style="top:886px">
  <div class="photo" role="img" aria-label="Pizza topped with tomatoes and basil" style="background:radial-gradient(circle at 45% 50%,#d98a3a,#8a2a18 65%,#3a1a10)"></div>
  <div>
    <div class="meta"><span><svg class="ico"><use href="#i-comment"/></svg>562</span><span><svg class="ico"><use href="#i-eye"/></svg>89</span><span><svg class="ico"><use href="#i-share"/></svg>8520</span></div>
    <h3 class="title">Lorem ipsum dolor sit amet, consecteter adipiscing elit, sed do eiusmod</h3>
    <p class="excerpt">There are many variations of passages of Lorem Ipsum available, but the majority have suffered alteration in some form, by injected umour, or randomised words which don't look even slightly believable.</p>
  </div>
</article>

<div class="abs sec-title" style="left:98px;top:1096px;width:637px"><span>Fun Stories</span></div>

<article class="abs story" style="left:98px;top:1173px">
  <div class="photo" role="img" aria-label="Couple eating pizza slices" style="background:linear-gradient(135deg,#b08a6a,#5a3e2e)"></div>
  <div class="meta"><span><svg class="ico"><use href="#i-comment"/></svg>562</span><span><svg class="ico"><use href="#i-eye"/></svg>89</span><span><svg class="ico"><use href="#i-share"/></svg>8520</span></div>
  <h3 class="title">I must explain to you how all this mistaken idea denouncing</h3>
</article>
<article class="abs story" style="left:429px;top:1173px">
  <div class="photo" role="img" aria-label="Group of friends at a pizza dinner" style="background:linear-gradient(135deg,#c7a07a,#6e4630)"></div>
  <div class="meta"><span><svg class="ico"><use href="#i-comment"/></svg>562</span><span><svg class="ico"><use href="#i-eye"/></svg>89</span><span><svg class="ico"><use href="#i-share"/></svg>8520</span></div>
  <h3 class="title">At vero eos et accusamus et iusto odio dignissimos ducimus</h3>
</article>
<article class="abs story" style="left:98px;top:1471px">
  <div class="photo" role="img" aria-label="Two friends laughing over pizza" style="background:linear-gradient(135deg,#e0cdb8,#9a6d50)"></div>
  <div class="meta"><span><svg class="ico"><use href="#i-comment"/></svg>562</span><span><svg class="ico"><use href="#i-eye"/></svg>89</span><span><svg class="ico"><use href="#i-share"/></svg>8520</span></div>
  <h3 class="title">Qui blanditiis praesentium volupta deleniti atque corrupti</h3>
</article>
<article class="abs story" style="left:429px;top:1471px">
  <div class="photo" role="img" aria-label="Friends sharing a pizza at a party" style="background:linear-gradient(135deg,#d8c8b8,#7a5a48)"></div>
  <div class="meta"><span><svg class="ico"><use href="#i-comment"/></svg>562</span><span><svg class="ico"><use href="#i-eye"/></svg>89</span><span><svg class="ico"><use href="#i-share"/></svg>8520</span></div>
  <h3 class="title">I must explain to you how all this mistaken idea denouncing</h3>
</article>

<div class="abs sec-title" style="left:98px;top:1786px;width:637px"><span>Our Videos</span></div>
<div class="abs video" role="img" aria-label="Video still of many pizzas on a dark counter">
  <svg class="play" viewBox="0 0 42 42"><circle cx="21" cy="21" r="19"/><path d="M17 13l11 8-11 8z" fill="#fff"/></svg>
</div>
<p class="abs video-text">Sed ut perspiciatis unde omnis iste natus error sit voluptatem accusantium doloremque laudantium, totam rem aperiam, eaque ipsa quae ab illo inventore veritatis et quasi architecto beatae vitae dicta sunt explicabo. Nemo enim ipsam voluptatem quia voluptas sit aspernatur aut odit aut fugit, sed quia consequuntur magni dolores eos qui ratione</p>
<div class="abs meta" style="left:98px;top:2241px"><span><svg class="ico"><use href="#i-comment"/></svg>562</span><span><svg class="ico"><use href="#i-eye"/></svg>89</span><span><svg class="ico"><use href="#i-share"/></svg>8520</span></div>

<div class="abs sec-title" style="left:98px;top:2302px;width:637px"><span>Our Employees Post</span></div>
<article class="abs emp" style="left:98px;top:2376px">
  <div class="photo" role="img" aria-label="Team sharing pizza around a table" style="background:linear-gradient(135deg,#b89878,#5e4636)"></div>
  <h3 class="title">Dolores et quas molestias excepturi sint</h3>
  <div class="meta"><span><svg class="ico"><use href="#i-comment"/></svg>562</span><span><svg class="ico"><use href="#i-eye"/></svg>89</span><span><svg class="ico"><use href="#i-share"/></svg>8520</span></div>
</article>
<article class="abs emp" style="left:320px;top:2376px">
  <div class="photo" role="img" aria-label="Pizza on a wooden board" style="background:linear-gradient(135deg,#e2a868,#a0481e)"></div>
  <h3 class="title">We denounce with riteous indignation</h3>
  <div class="meta"><span><svg class="ico"><use href="#i-comment"/></svg>562</span><span><svg class="ico"><use href="#i-eye"/></svg>89</span><span><svg class="ico"><use href="#i-share"/></svg>8520</span></div>
</article>
<article class="abs emp" style="left:540px;top:2376px">
  <div class="photo" role="img" aria-label="Pizza with peppers and basil" style="background:radial-gradient(circle,#d8702e,#7a2a16 70%)"></div>
  <h3 class="title">The wise man therefore to always holds</h3>
  <div class="meta"><span><svg class="ico"><use href="#i-comment"/></svg>562</span><span><svg class="ico"><use href="#i-eye"/></svg>89</span><span><svg class="ico"><use href="#i-share"/></svg>8520</span></div>
</article>

<div class="abs sec-title side" style="top:584px"><span>Follow Us</span></div>
<div class="abs side follow" style="top:660px">
  <a style="background:var(--pagebook)"><span class="sq"><i></i></span><span class="count">194,598</span>Follow us on <b>&nbsp;Pagebook</b></a>
  <a style="background:var(--chirper)"><span class="sq"><i></i></span><span class="count">194,598</span>Follow us on <b>&nbsp;Chirper</b></a>
  <a style="background:var(--viewtube)"><span class="sq"><i></i></span><span class="count">194,598</span>Follow us on <b>&nbsp;ViewTube</b></a>
  <a style="background:var(--snapgram)"><span class="sq"><i></i></span><span class="count">194,598</span>Follow us on <b>&nbsp;Snapgram</b></a>
</div>

<div class="abs sec-title side" style="top:858px"><span>Most Popular</span></div>
<article class="abs side popular" style="top:931px">
  <div class="photo" role="img" aria-label="Friends biting into pizza slices" style="background:linear-gradient(135deg,#e4d4c4,#a07858)"></div>
  <p>Excepteur sint occaecat the cupidatat non proident, sunt in culpa qui</p>
  <div class="row"><span>January 24, 2017</span><span><svg class="ico"><use href="#i-comment"/></svg>562</span></div>
</article>
<article class="abs side popular" style="top:1216px">
  <div class="photo" role="img" aria-label="Diners at a pizza restaurant" style="background:linear-gradient(135deg,#d49a5a,#6a4028)"></div>
  <p>Excepteur sint occaecat the cupidatat non proident, sunt in culpa qui</p>
  <div class="row"><span>January 24, 2017</span><span><svg class="ico"><use href="#i-comment"/></svg>562</span></div>
</article>
<article class="abs side popular" style="top:1500px">
  <div class="photo" role="img" aria-label="Hands reaching for pizza slices" style="background:linear-gradient(135deg,#c8884a,#5a3422)"></div>
  <p>Excepteur sint occaecat the cupidatat non proident, sunt in culpa qui</p>
  <div class="row"><span>January 24, 2017</span><span><svg class="ico"><use href="#i-comment"/></svg>562</span></div>
</article>

<form class="abs comments">
  <h3>POST YOUR COMMENTS</h3>
  <p>Sed ut perspiciatis unde omni iste natus error voluptatem accusantium dolore</p>
  <div class="field">Your Mail id</div>
  <div class="field area">Comments</div>
  <div class="submit">SUBMIT NOW</div>
</form>

<div class="abs sec-title side" style="top:2108px"><span>Recent Post</span></div>
<article class="abs side recent" style="top:2182px">
  <div class="photo" role="img" aria-label="Pizza slice being served" style="background:linear-gradient(135deg,#a88468,#4a3226)"></div>
  <div><h3 class="title">On the other hand the we denounce righteous</h3><p class="excerpt">If you use this site regularly and would like to help keep</p></div>
</article>
<article class="abs side recent" style="top:2329px">
  <div class="photo" role="img" aria-label="Person eating pizza" style="background:linear-gradient(135deg,#e2ccb4,#a47c5c)"></div>
  <div><h3 class="title">He rejects pleasures to secure other greater</h3><p class="excerpt">If you use this site regularly and would like to help keep</p></div>
</article>
<article class="abs side recent" style="top:2482px">
  <div class="photo" role="img" aria-label="Cozy pizza restaurant interior" style="background:linear-gradient(135deg,#b89070,#54382a)"></div>
  <div><h3 class="title">The wise man therefore always holds</h3><p class="excerpt">If you use this site regularly and would like to help keep</p></div>
</article>

<div class="abs divider"></div>
<h2 class="abs gallery-title">OUR PICTURE GALLERY</h2>
<div class="abs gal-nav">
  <svg viewBox="0 0 24 24"><circle cx="12" cy="12" r="10"/><path d="M14 7l-5 5 5 5"/></svg>
  <svg viewBox="0 0 24 24"><circle cx="12" cy="12" r="10"/><path d="M10 7l5 5-5 5"/></svg>
</div>
<div class="abs gallery">
  <div class="photo" role="img" aria-label="Sliced pizza on a board" style="background:radial-gradient(circle,#d88a3e,#6a3020 70%)"></div>
  <div class="photo" role="img" aria-label="Pizza with tomatoes on a table" style="background:linear-gradient(135deg,#e4b888,#a8542a)"></div>
  <div class="photo" role="img" aria-label="Pizza with peppers" style="background:radial-gradient(circle,#e09040,#8a3a1a 70%)"></div>
  <div class="photo" role="img" aria-label="Cheese pizza close-up" style="background:linear-gradient(135deg,#e8c494,#b46a34)"></div>
  <div class="photo" role="img" aria-label="Friends at a pizza table" style="background:linear-gradient(135deg,#d0b8a0,#7a5844)"></div>
</div>

<div class="abs partners">
  <div class="partner">Marlo's Pizzeria</div>
  <div class="partner">Marlo's Pizzeria</div>
  <div class="partner">Northside Pies</div>
  <div class="partner">Marlo's Pizzeria</div>
</div>

<footer class="abs site-footer">
  <div class="logo">Bim-Zee</div>
  <nav class="foot-nav">Home<b>/</b>About us<b>/</b>News<b>/</b>Funs<b>/</b>Stories<b>/</b>Pictures<b>/</b>Contact us</nav>
  <div class="socials"><i></i><i></i><i></i><i></i><i></i><i></i></div>
  <div class="copy">Copyright@2017company name</div>
</footer>
</body>
</html>
```